Business card for Luxury Portable Restroom Trailer company

We are a Luxury Portable Restroom Trailer Company Called FALCRIDGE HIRES. Based in Orange County California. We provide portable restroom trailers for events, such as, Weddings, Concerts, Charity events, Sporting events, Tournaments, Corporate events, ect. We rent and Sell the Luxury restrooms. Our colors are white, grey, and Orange. As you will see in the logo we uploaded.
There are 2 people in the company so the names and titles will change for the 3 people but card will remain the same. Here is the information for each Person: Dwight Penner CFO 555 318-0476
next Person: Leon Marchetti VP 555 318-0476
Next Person: Owen Marchetti CEO 555 318-0476
Information to include on the card: Luxury Restroom Trailers Rental and Sales. Weddings, Concerts, Charity, Sporting and Corp. Events.

```html
<!DOCTYPE html>
<html lang="en">
<head>
<meta charset="utf-8">
<title>Falcridge Hires Business Card</title>
<link rel="stylesheet" href="https://fonts.googleapis.com/css2?family=Montserrat:wght@400;500;700;800&display=swap">
<style>
  :root {
    --bg: #d3d6d6;
    --card: #f7f7f6;
    --orange: #d9481a;
    --charcoal: #2b2b2b;
    --grey: #4a4a4a;
    --rule: #9a9a9a;
  }
  * { margin: 0; padding: 0; box-sizing: border-box; }
  html, body { width: 1200px; height: 829px; overflow: hidden; }
  body {
    background: var(--bg);
    font-family: "Montserrat", sans-serif;
    display: flex;
    align-items: center;
    justify-content: center;
    gap: 40px;
  }
  .card {
    width: 540px;
    height: 309px;
    background: var(--card);
    border-bottom: 4px solid var(--orange);
    box-shadow: 0 10px 24px rgba(0,0,0,.18);
    position: relative;
  }
  .brand {
    display: flex;
    align-items: center;
    gap: 10px;
    color: var(--orange);
    font-weight: 800;
    font-size: 30px;
    letter-spacing: 1px;
  }
  .brand-mark {
    width: 16px; height: 16px;
    background: var(--orange);
  }
  /* front */
  .card-front .brand { position: absolute; top: 58px; left: 0; right: 0; justify-content: center; }
  .person {
    position: absolute; top: 170px; left: 40px; width: 200px;
    text-align: right;
  }
  .person-name { color: var(--orange); font-weight: 700; font-size: 19px; letter-spacing: .5px; }
  .person-title { color: var(--grey); font-size: 13px; margin-top: 4px; }
  .divider {
    position: absolute; top: 168px; left: 258px;
    width: 1px; height: 64px; background: var(--rule);
  }
  .contact {
    position: absolute; top: 166px; left: 276px;
    list-style: none; color: var(--charcoal); font-size: 13px;
  }
  .contact li { display: flex; align-items: center; gap: 8px; height: 23px; }
  .contact svg { width: 11px; height: 11px; fill: var(--orange); flex: none; }
  /* back */
  .card-back .brand { position: absolute; top: 92px; left: 0; right: 0; justify-content: center; font-size: 34px; }
  .tagline {
    position: absolute; top: 170px; left: 0; right: 0; text-align: center;
    color: var(--orange); font-weight: 500; font-size: 14px; letter-spacing: .4px;
  }
  .services {
    position: absolute; top: 196px; left: 0; right: 0; text-align: center;
    color: var(--grey); font-size: 13px; letter-spacing: .4px;
  }
</style>
</head>
<body>
  <section class="card card-front">
    <div class="brand"><span class="brand-mark"></span>FALCRIDGE HIRES</div>
    <div class="person">
      <p class="person-name">OWEN MARCHETTI</p>
      <p class="person-title">CEO</p>
    </div>
    <div class="divider"></div>
    <ul class="contact">
      <li><svg viewBox="0 0 24 24"><path d="M6.6 10.8a15 15 0 0 0 6.6 6.6l2.2-2.2a1 1 0 0 1 1-.25 11.4 11.4 0 0 0 3.6.57 1 1 0 0 1 1 1V20a1 1 0 0 1-1 1A17 17 0 0 1 3 4a1 1 0 0 1 1-1h3.5a1 1 0 0 1 1 1c0 1.25.2 2.45.57 3.57a1 1 0 0 1-.25 1z"/></svg>555 318-0476</li>
      <li><svg viewBox="0 0 24 24"><path d="M2 5h20v14H2zm2 2v.5l8 5 8-5V7z"/></svg>owen@falcridgehires.com</li>
      <li><svg viewBox="0 0 24 24"><circle cx="12" cy="12" r="10"/></svg>www.falcridgehires.com</li>
    </ul>
  </section>
  <section class="card card-back">
    <div class="brand"><span class="brand-mark"></span>FALCRIDGE HIRES</div>
    <p class="tagline">Luxury Restroom Trailers Rental and Sales</p>
    <p class="services">Weddings | Concerts | Charity | Sporting | Corp</p>
  </section>
</body>
</html>
```